Accounting firm needing business card / letterhead designed
Marcus L. Trenholm, CPA
marcus@veltrowledger.com
www.veltrowledger.com
842 E Alder Ave Dunmore Falls, MI 43827
419-562-0974

```html
<!DOCTYPE html>
<html lang="en">
<head>
<meta charset="utf-8">
<title>Veltro Ledger – Business Card</title>
<link href="https://fonts.googleapis.com/css2?family=Roboto:wght@400;700&family=Roboto+Condensed:wght@700&display=swap" rel="stylesheet">
<style>
  :root {
    --backdrop: #e4e4e4;
    --paper: #f4f4f4;
    --navy: #241f5d;
    --lime: #8cc63f;
    --ink: #555555;
    --rule: #cfcfcf;
    --white: #ffffff;
  }
  * { margin: 0; padding: 0; box-sizing: border-box; }
  html, body {
    width: 1200px;
    height: 960px;
    overflow: hidden;
    background: var(--backdrop);
    font-family: "Roboto", Arial, sans-serif;
  }
  .canvas { position: relative; width: 1200px; height: 960px; }

  .card { position: absolute; width: 600px; height: 343px; overflow: hidden; }

  /* Front */
  .card-front { left: 314px; top: 113px; background: var(--paper); }
  .front-brand {
    position: absolute; left: 40px; top: 0; width: 250px; height: 320px;
    display: flex; align-items: center; justify-content: center;
  }
  .brand-name {
    font-family: "Roboto", Arial, sans-serif;
    font-weight: 700;
    letter-spacing: 1px;
    white-space: nowrap;
  }
  .front-brand .brand-name { font-size: 28px; color: var(--navy); }
  .divider {
    position: absolute; left: 306px; top: 92px;
    width: 1px; height: 155px; background: var(--rule);
  }
  .contact { position: absolute; left: 332px; top: 100px; color: var(--ink); }
  .contact-name {
    font-family: "Roboto Condensed", "Arial Narrow", sans-serif;
    font-weight: 700; font-size: 22px; color: var(--navy);
    line-height: 26px; margin-bottom: 8px;
  }
  .contact-address { font-size: 14px; line-height: 18px; margin-bottom: 11px; }
  .contact-line {
    display: flex; align-items: center; gap: 8px;
    font-size: 14px; line-height: 19px;
  }
  .contact-line svg { width: 14px; height: 14px; fill: var(--navy); flex: none; }
  .accent-rule { position: absolute; left: 0; top: 321px; width: 600px; height: 3px; background: var(--lime); }
  .base-band { position: absolute; left: 0; top: 324px; width: 600px; height: 19px; background: var(--navy); }

  /* Back */
  .card-back {
    left: 311px; top: 472px; background: var(--navy);
    display: flex; flex-direction: column; align-items: center;
  }
  .card-back .brand-name { margin-top: 128px; font-size: 46px; color: var(--white); }
  .back-url {
    position: absolute; left: 0; right: 0; top: 282px; text-align: center;
    font-size: 14px; letter-spacing: 5px; color: var(--white);
  }
</style>
</head>
<body>
<main class="canvas">
  <section class="card card-front">
    <div class="front-brand"><span class="brand-name">VELTRO LEDGER</span></div>
    <div class="divider"></div>
    <div class="contact">
      <p class="contact-name">Marcus L. Trenholm, CPA</p>
      <p class="contact-address">842 E Alder Ave<br>Dunmore Falls, MI 43827</p>
      <p class="contact-line">
        <svg viewBox="0 0 24 24" aria-hidden="true"><path d="M6.6 10.8a15.1 15.1 0 0 0 6.6 6.6l2.2-2.2a1 1 0 0 1 1-.25 11.4 11.4 0 0 0 3.6.57 1 1 0 0 1 1 1V20a1 1 0 0 1-1 1A17 17 0 0 1 3 4a1 1 0 0 1 1-1h3.5a1 1 0 0 1 1 1c0 1.25.2 2.45.57 3.57a1 1 0 0 1-.25 1z"/></svg>
        419-562-0974
      </p>
      <p class="contact-line">
        <svg viewBox="0 0 24 24" aria-hidden="true"><path d="M2 5h20v14H2z M3 6.5v1l9 6 9-6v-1l-9 6z" fill-rule="evenodd"/></svg>
        marcus@veltrowledger.com
      </p>
      <p class="contact-line">
        <svg viewBox="0 0 24 24" aria-hidden="true"><circle cx="12" cy="12" r="10"/><path d="M7 7c2 1 3 0 4 2s-2 3 0 5 1 4 1 6M14 4c0 2 2 3 4 3M15 13c2 0 3 1 3 3" stroke="#f4f4f4" stroke-width="1.6" fill="none"/></svg>
        www.veltrowledger.com
      </p>
    </div>
    <div class="accent-rule"></div>
    <div class="base-band"></div>
  </section>

  <section class="card card-back">
    <span class="brand-name">VELTRO LEDGER</span>
    <p class="back-url">www.veltrowledger.com</p>
  </section>
</main>
</body>
</html>
```